Website Banner Design Needed for Health/Medical Business

We are looking for a creative and professional set of banners for the front page of our:
1. website - kelvoramedics.com.au and lunetaskin.com.au and bluemoorcare.com.au

then edit the above banners to the corrrect sizes for below
2. Our facebook pages (1 for each of the above websites)

3. Our google + pages (2 in total one for melb and syd)

4. You tube pages (1 for kelvoramedics and 1 for lunetaskin)

We are looking for something fresh and clean that gives the feeling of:
1. Medical (dont show pictures of doctors though - nurses are ok - just not doctors)
2. Modern because PRP is a modern medical procedure
3. Most Experienced - No other clinic in Australia has performed as many PRP treatments compared to us.
4. We offer a 100% money back guarantee as well

The banners will not be animated or using layers. they will be still banners.

We would prefer to use new stock images and will purchase them for you after you have provided some suggestions/initial drafts.

Target Market(s)

men and women from 25-65

Industry/Entity Type

Health And Wellness

Number of Pages Required

1 page

Font styles to use
Sans Serif

Requirements
Must have
• no doctor images
• nurses are ok - but no doctor images
• for the images avoid fake themed images eg. a person looking in the mirror at their hair loss = NO NO NO..... instead aim for a nurse holding a test tube or a clipboard .
• The banners need to emphasise we are the only clinic who has performed 11,000+ treatments in australia
Nice to have
• a medical feeling would be nice - but dont make it too medical. i want the viewer to associate the word TRUSTED PROVEN and RELIABLE when they view the banner.
Should not have
• as mentioned no doctor or images that look like hospital too much.
• we are a private clinic run by nurses - i have to becareful not to mislead the viewer

```html
<!DOCTYPE html>
<html lang="en">
<head>
<meta charset="utf-8">
<title>PRP Clinic Banner</title>
<link rel="stylesheet" href="https://fonts.googleapis.com/css2?family=Montserrat:ital,wght@0,300;0,400;1,600;1,800&family=Roboto+Condensed:wght@700&family=Great+Vibes&display=swap">
<style>
  :root {
    --stage: #e9eaec;
    --brand-blue: #3c61a5;
    --text-blue: #2f4f91;
    --badge-blue: #2e8ad0;
    --brand-green: #4fbf63;
    --bar-green: #86e08f;
    --white: #ffffff;
    --photo-light: #f4f1e4;
    --photo-mid: #c9cdbf;
    --photo-dark: #8f9c95;
  }
  * { box-sizing: border-box; margin: 0; padding: 0; }
  html, body { width: 1200px; height: 612px; overflow: hidden; background: var(--stage); }
  .stage { position: relative; width: 1200px; height: 612px; }
  .banner {
    position: absolute; left: 20px; top: 88px;
    width: 1308px; height: 492px;
    transform: scale(0.8869); transform-origin: 0 0;
    overflow: hidden; background: var(--white);
    font-family: "Montserrat", sans-serif;
  }
  .photo {
    position: absolute; inset: 0;
    background:
      radial-gradient(ellipse at 58% 25%, #fffef6 0%, rgba(255,254,246,0) 45%),
      linear-gradient(100deg, var(--photo-dark) 0%, var(--photo-mid) 35%, var(--photo-light) 55%, var(--photo-mid) 85%);
  }
  .shapes { position: absolute; inset: 0; }
  .headline-box {
    position: absolute; left: 742px; top: 35px; width: 566px; height: 110px;
    background: var(--white); padding: 14px 0 0 42px; color: var(--text-blue);
  }
  .headline-lead { font-weight: 400; font-size: 31px; line-height: 38px; }
  .headline-main { font-weight: 800; font-style: italic; font-size: 40px; line-height: 48px; }
  .tagline-bar {
    position: absolute; left: 865px; top: 148px; width: 443px; height: 58px;
    background: var(--bar-green); color: var(--white);
    font-family: "Great Vibes", cursive; font-size: 44px; line-height: 60px; padding-left: 26px;
  }
  .features { position: absolute; left: 887px; top: 224px; list-style: none; }
  .feature {
    display: flex; align-items: center; gap: 10px; height: 41px;
    color: var(--text-blue); font-weight: 600; font-style: italic; font-size: 20px;
  }
  .feature svg { width: 16px; height: 16px; fill: var(--text-blue); }
  .guarantee-badge {
    position: absolute; left: -28px; top: 300px; width: 240px; height: 190px;
    background: var(--badge-blue); border-radius: 26px;
    transform: rotate(28deg); transform-origin: 50% 50%;
    color: var(--white); font-family: "Roboto Condensed", sans-serif; font-weight: 700;
    padding: 22px 0 0 58px; line-height: 1;
  }
  .guarantee-figure { font-size: 62px; letter-spacing: -1px; }
  .guarantee-figure span { font-size: 38px; }
  .guarantee-words { font-size: 27px; line-height: 28px; margin-top: 4px; }
</style>
</head>
<body>
<div class="stage">
  <div class="banner">
    <div class="photo" role="img" aria-label="Photo of a nurse smiling at an older man holding a tablet in a bright clinic room"></div>

    <svg class="shapes" viewBox="0 0 1308 492" width="1308" height="492" aria-hidden="true">
      <path d="M0,0 L18,0 C40,160 140,420 318,492 L0,492 Z" fill="var(--brand-green)"/>
      <path d="M0,200 C50,330 140,440 262,492 L0,492 Z" fill="var(--white)"/>
      <path d="M845,0 L1308,0 L1308,492 L1220,492 C1195,300 1085,115 845,0 Z" fill="var(--brand-blue)"/>
    </svg>

    <div class="headline-box">
      <p class="headline-lead">Only Australian clinic to perform</p>
      <p class="headline-main">11,000+ PRP Treatments</p>
    </div>

    <div class="tagline-bar">Reliable &amp; Trusted</div>

    <ul class="features">
      <li class="feature">
        <svg viewBox="0 0 16 16"><circle cx="8" cy="5" r="3.5"/><path d="M1.5,16 C1.5,10 14.5,10 14.5,16 Z"/></svg>
        Trained Staff
      </li>
      <li class="feature">
        <svg viewBox="0 0 16 16"><path d="M3,1 V7 A4,4 0 0 0 11,7 V1" fill="none" stroke="var(--text-blue)" stroke-width="2"/><path d="M7,11 V13 A2,2 0 0 0 13,13 V10" fill="none" stroke="var(--text-blue)" stroke-width="2"/><circle cx="13" cy="9" r="2"/></svg>
        Reliable Equipment
      </li>
      <li class="feature">
        <svg viewBox="0 0 16 16"><path d="M8,0 L15,3 V8 C15,12 11,15 8,16 C5,15 1,12 1,8 V3 Z"/><circle cx="8" cy="8" r="2.5" fill="var(--white)"/></svg>
        Best Consultancy
      </li>
    </ul>

    <div class="guarantee-badge">
      <p class="guarantee-figure">100<span>%</span></p>
      <p class="guarantee-words">Money Back<br>Guarantee</p>
    </div>
  </div>
</div>
</body>
</html>
```